Custom Manufacturing Company square space website design

I own a custom manufacturing company that uses precision cutting technology to manufacture project components over a couple industries. We have an industrial CNC router and state of the art edge bander and cut a lot of cabinetry components for cabinet shops, builders, closet companies, ect. We offer design and assembly for any cabinetry or can build cabinets to spec. We also cut components for other industries out of wood, plastics, acryclics, ect. We offer design engineering services, product development protype services. we have a 3D printer farm. We want our communicate trust, dependability, and the value we place on client relationships.

We essentially want a credibility website. Landing page and drops downs for services we offer, capabilites, about us, contact

```html
<!DOCTYPE html>
<html lang="en">
<head>
<meta charset="utf-8">
<title>Riverbend CNC</title>
<link href="https://fonts.googleapis.com/css2?family=Oswald:wght@300;400;500;600&family=Montserrat:wght@400;500;600;700&display=swap" rel="stylesheet">
<style>
:root{
  --ink:#111111;
  --dark:#1c1c1c;
  --grey:#e6e6e6;
  --muted:#555555;
  --white:#ffffff;
  --wood:#b98d62;
  --cream:#f1eee9;
  --navy:#26324a;
}
*{box-sizing:border-box;margin:0;padding:0}
html,body{width:1200px;height:3762px;overflow:hidden}
body{position:relative;background:var(--white);font-family:'Montserrat',sans-serif;color:var(--ink)}
.display{font-family:'Oswald',sans-serif;text-transform:uppercase;letter-spacing:-.5px;line-height:1}
.display .light{font-weight:300}
.display .bold{font-weight:600}
.btn{position:absolute;display:flex;align-items:center;justify-content:center;font-weight:700;font-size:14px;text-transform:uppercase;border-radius:3px}
.btn-dark{background:var(--ink);color:var(--white)}
.btn-light{background:var(--white);color:var(--ink)}
.photo{position:absolute}

/* header */
.site-header{position:absolute;left:0;top:0;width:1200px;height:78px;background:var(--white);border-top:3px solid var(--ink)}
.brand{position:absolute;left:105px;top:20px;display:flex;align-items:center;gap:12px;font-weight:700;font-size:22px;letter-spacing:2px}
.brand .mark{width:28px;height:28px;background:var(--ink)}
.nav{position:absolute;top:28px;font-size:14px;color:var(--muted)}
.nav.active{color:var(--ink);font-weight:600}
.nav-cta{left:933px;top:14px;width:153px;height:46px}

/* hero */
.hero-photo{left:0;top:78px;width:1200px;height:615px;
  background:
    linear-gradient(180deg,rgba(255,255,255,0) 55%,rgba(232,232,230,.9) 75%,#f2f2f1 100%),
    linear-gradient(90deg,#c7a47d 0%,#e6d6c2 14%,#f3f1ee 32%,#ecebea 55%,#e2e2e0 74%,#3a3a3a 84%,#151515 92%,#6f8a5a 100%)}
.hero-box{position:absolute;left:275px;top:208px;width:650px;height:325px;background:rgba(150,150,150,.45);border:4px solid #3a3a3a;text-align:center}
.hero-title{font-size:80px;font-weight:600;margin-top:38px}
.hero-sub{font-size:21px;line-height:33px;margin:20px auto 0;width:560px}
.hero-btn{left:249px;top:221px;width:152px;height:46px}
.dot{position:absolute;top:647px;width:12px;height:12px;border-radius:50%;background:#777}
.dot.on{background:var(--ink)}

/* services */
.section-title{position:absolute;left:0;width:1200px;text-align:center;font-size:52px}
.card{position:absolute;top:858px;width:308px;height:408px;background:var(--white);border-radius:6px;box-shadow:0 2px 10px rgba(0,0,0,.18)}
.card .photo{left:8px;top:8px;width:293px;height:202px;border-radius:4px}
.card h3{position:absolute;left:20px;top:222px;font-size:30px;font-weight:400;line-height:35px}
.card p{position:absolute;left:20px;top:298px;width:275px;font-size:15.5px;line-height:24px;color:var(--muted)}
.card .btn{left:26px;top:390px;width:128px;height:36px;font-family:'Oswald',sans-serif;font-size:13px;letter-spacing:1.5px}
.arrow{position:absolute;top:1031px;width:62px;height:62px;border-radius:50%;background:var(--ink)}

/* about */
.about-photo{left:0;top:1371px;width:590px;height:513px;
  background:
    linear-gradient(180deg,rgba(255,255,255,0) 50%,rgba(190,170,140,.55) 72%,#e4e2de 100%),
    linear-gradient(90deg,#2a2a2a 0%,#8f8b84 10%,#e9e6e1 22%,#f4f3f1 50%,#e7e6e3 80%,#cfcac1 100%)}
.about-panel{position:absolute;left:590px;top:1371px;width:610px;height:513px;background:var(--dark);color:var(--white)}
.about-panel h2{position:absolute;left:27px;top:78px;font-size:52px}
.about-panel p{position:absolute;left:27px;top:144px;width:480px;font-size:17px;line-height:26.5px;text-align:justify}
.about-panel .btn{left:27px;top:380px;width:152px;height:47px}

/* capabilities */
.capabilities{position:absolute;left:0;top:1884px;width:1200px;height:828px;background:var(--grey)}
.cap-frame{position:absolute;left:220px;top:151px;width:760px;height:358px;border:8px solid #222;
  background:linear-gradient(180deg,#cfd0d1 0%,#e4e4e4 22%,#f5f4f2 45%,#fafafa 62%,#d6d6d6 70%,#c4c5c6 100%)}
.cap-text{position:absolute;left:190px;top:536px;width:820px;font-size:16.5px;line-height:26.5px;text-align:justify;text-align-last:center}
.cap-btn{left:524px;top:694px;width:152px;height:47px}

/* contact */
.contact-title{left:112px;top:2792px;font-size:52px;text-align:left;width:auto}
.contact-intro{position:absolute;left:116px;top:2860px;width:400px;font-size:16.5px;line-height:26.5px}
.info{position:absolute;left:113px;display:flex;gap:24px}
.info .icon{width:46px;height:46px;border-radius:50%;background:var(--ink);flex:none;display:flex;align-items:center;justify-content:center;margin-top:4px}
.info .label{font-size:16px;color:#777;line-height:22px}
.info .value{font-size:18px;line-height:26px;font-weight:500}
.field{position:absolute;left:577px;width:501px;height:49px;background:var(--ink);color:var(--white);border-radius:3px;font-size:15px;padding:16px 21px}
.submit{left:577px;top:3203px;width:152px;height:47px;border:2px solid var(--ink);background:var(--white);color:var(--ink)}

/* footer */
.site-footer{position:absolute;left:0;top:3335px;width:1200px;height:427px;background:linear-gradient(180deg,#262626,#161616)}
.foot-brand{position:absolute;left:145px;top:120px;display:flex;align-items:center;gap:14px;color:var(--white);font-weight:700;font-size:26px;letter-spacing:3px}
.foot-brand .mark{width:30px;height:30px;background:var(--white)}
.col{position:absolute;top:80px;color:var(--white)}
.col h4{font-size:17px;font-weight:700;border-left:5px solid var(--white);padding-left:17px;line-height:26px}
.col .rule{width:50px;height:2px;background:var(--white);margin:12px 0 16px 22px}
.col ul{list-style:none;padding-left:22px;font-size:13px;line-height:26px}
.foot-rule{position:absolute;left:90px;top:320px;width:1000px;height:1px;background:#444}
.copyright{position:absolute;left:0;top:358px;width:1200px;text-align:center;font-size:14px;color:var(--white)}
.to-top{position:absolute;left:1115px;top:316px;width:40px;height:40px;border-radius:6px;background:var(--white);display:flex;align-items:center;justify-content:center}
</style>
</head>
<body>

<header class="site-header">
  <div class="brand"><span class="mark"></span>RIVERBEND CNC</div>
  <span class="nav active" style="left:437px">Home</span>
  <span class="nav" style="left:526px">Services We Offer</span>
  <span class="nav" style="left:695px">Capabilities</span>
  <span class="nav" style="left:826px">About Us</span>
  <span class="btn btn-dark nav-cta">Contact Us</span>
</header>

<section>
  <div class="photo hero-photo" role="img" aria-label="Bright white kitchen with wooden shelves and counter, black range hood and black refrigerator with plants"></div>
  <div class="hero-box">
    <h1 class="display hero-title">Riverbend CNC</h1>
    <p class="hero-sub">Saers Ikses sepiciatis unde omnisiste natuserrorsit voluptatem ascсu.</p>
    <span class="btn btn-dark hero-btn">Get Started</span>
  </div>
  <span class="dot" style="left:562px"></span>
  <span class="dot on" style="left:583px"></span>
  <span class="dot" style="left:604px"></span>
  <span class="dot" style="left:625px"></span>
</section>

<section>
  <h2 class="display section-title" style="top:775px"><span class="light">Our </span><span class="bold">Services</span></h2>
  <svg class="arrow" style="left:38px" viewBox="0 0 62 62"><path d="M42 31H20M29 22l-9 9 9 9" stroke="#fff" stroke-width="3" fill="none" stroke-linecap="round" stroke-linejoin="round"/></svg>
  <svg class="arrow" style="left:1098px" viewBox="0 0 62 62"><path d="M20 31h22M33 22l9 9-9 9" stroke="#fff" stroke-width="3" fill="none" stroke-linecap="round" stroke-linejoin="round"/></svg>

  <article class="card" style="left:112px">
    <div class="photo" role="img" aria-label="Navy blue shaker cabinet doors with brass handles" style="background:linear-gradient(160deg,#34425e 0%,#26324a 45%,#1b2336 85%,#0f0f0f 100%)"></div>
    <h3 class="display">Custom Cabinet<br>Design</h3>
    <p>Saerspiciatis unde omnis iste natus error sit voluptatem doloremqueasds laudantiumotam.</p>
    <span class="btn btn-dark">Learn More</span>
  </article>
  <article class="card" style="left:445px">
    <div class="photo" role="img" aria-label="Open walnut drawer in wooden cabinetry" style="background:linear-gradient(160deg,#6b4a35 0%,#9c7656 35%,#b8926c 60%,#8a6a4e 100%)"></div>
    <h3 class="display">Cabinet<br>Construction</h3>
    <p>Saerspiciatis unde omnis iste natus error sit voluptatem doloremqueasds laudantiumotam.</p>
    <span class="btn btn-dark">Learn More</span>
  </article>
  <article class="card" style="left:778px">
    <div class="photo" role="img" aria-label="Installed white kitchen cabinets with island and wood floor" style="background:linear-gradient(180deg,#f4f3f1 0%,#ecebe8 55%,#c9bba9 78%,#8d725a 100%)"></div>
    <h3 class="display">Kitchen Cabinet<br>Installation</h3>
    <p>Saerspiciatis unde omnis iste natus error sit voluptatem doloremqueasds laudantiumotam.</p>
    <span class="btn btn-dark">Learn More</span>
  </article>
</section>

<section>
  <div class="photo about-photo" role="img" aria-label="White kitchen with open wooden shelves beside a wooden dining table and black chairs"></div>
  <div class="about-panel">
    <h2 class="display"><span class="light">About </span><span class="bold">Us</span></h2>
    <p>Saerspiciatis undeasepoiise oklasdo mnis aidaste natus error sit voluptatem accusan tium doloremque laudantium, totam rem aperiam, ease aque ipaefdsa quae ab illo inventore veritatis ease quasi architecto beatae vitae dicta sunt explicabo. Nemo enim ipsam voluptatem quia volasdfupta sde sessitasese aspernatur autodit aut fugitsdsed quisaea consequuntur magni dolores eos qui ratione voluptatem sequi nesciunt.</p>
    <span class="btn btn-light">Read More</span>
  </div>
</section>

<section class="capabilities">
  <h2 class="display section-title" style="top:81px;font-weight:400">Capabilities</h2>
  <div class="cap-frame" role="img" aria-label="Light grey shaker kitchen cabinets with range hood and gas hob"></div>
  <p class="cap-text">Saerspiciatis undeasepoiise oklasdo mnis aidaste natus error sit voluptatem accusan tium doloremque laudantium, totam rem aperiam, ease aque ipaefdsa quae ab illo inventore veritatis ease quasi architecto beatae vitae dicta sunt explicabo. Nemo enim ipsam voluptatem quia volasdfupta sde sessitasese aspernatur autodit aut fugitsdsed quisaea consequuntur magni dolores eos qui ratione voluptatem sequi nesciunt.</p>
  <span class="btn btn-dark cap-btn">Learn More</span>
</section>

<section>
  <h2 class="display section-title contact-title"><span class="light">Contact </span><span class="bold">Us</span></h2>
  <p class="contact-intro">Saerspiciatis undeasepoiise oklasdo mnis aidaste natus error sit voluptatem accusan tium doloremque laudantium, totam rem</p>

  <div class="info" style="top:2977px">
    <span class="icon"><svg width="20" height="24" viewBox="0 0 20 24"><path d="M10 1a8 8 0 0 0-8 8c0 6 8 14 8 14s8-8 8-14a8 8 0 0 0-8-8z" fill="#fff"/><circle cx="10" cy="9" r="3" fill="#111"/></svg></span>
    <div><div class="label">Address</div><div class="value">42 Millstone Ave, Harlow<br>Kingsford, Canada, 55012</div></div>
  </div>
  <div class="info" style="top:3072px">
    <span class="icon"><svg width="22" height="22" viewBox="0 0 24 24"><path d="M6.6 10.8a15 15 0 0 0 6.6 6.6l2.2-2.2c.3-.3.7-.4 1-.2 1.1.4 2.3.6 3.6.6.6 0 1 .4 1 1V20c0 .6-.4 1-1 1C10.6 21 3 13.4 3 4c0-.6.4-1 1-1h3.5c.6 0 1 .4 1 1 0 1.3.2 2.5.6 3.6.1.3 0 .7-.2 1z" fill="#fff"/></svg></span>
    <div><div class="label">Call Us</div><div class="value">+1 (555) 014-2290</div></div>
  </div>
  <div class="info" style="top:3145px">
    <span class="icon"><svg width="22" height="16" viewBox="0 0 22 16"><rect x="1" y="1" width="20" height="14" rx="2" fill="#fff"/><path d="M2 2l9 7 9-7" stroke="#111" stroke-width="1.6" fill="none"/></svg></span>
    <div><div class="label">Email</div><div class="value">hello@riverbendcnc.com</div></div>
  </div>

  <div class="field" style="top:2798px">Your Name</div>
  <div class="field" style="top:2868px">Email</div>
  <div class="field" style="top:2937px">Phone Number</div>
  <div class="field" style="top:3007px;height:180px">Address</div>
  <span class="btn submit">Submit</span>
</section>

<footer class="site-footer">
  <div class="foot-brand"><span class="mark"></span>RIVERBEND CNC</div>
  <div class="col" style="left:492px">
    <h4>QUICK LINKS</h4><div class="rule"></div>
    <ul><li>HOME</li><li>SERVICES WE OFFER</li><li>CAPABILITIES</li><li>ABOUT US</li><li>CONTACT US</li></ul>
  </div>
  <div class="col" style="left:770px">
    <h4>LINKS</h4><div class="rule"></div>
    <ul><li>COPYRIGHT</li><li>LEGAL</li><li>PRIVACY</li><li>ACCESSIBILITY</li><li>SITEMAP</li></ul>
  </div>
  <div class="col" style="left:973px">
    <h4>SUPPORT</h4><div class="rule"></div>
    <ul><li>TEAM</li><li>ABOUT US</li><li>CAREERS</li><li>OUR VALUES</li></ul>
  </div>
  <div class="foot-rule"></div>
  <div class="to-top"><svg width="14" height="10" viewBox="0 0 14 10"><path d="M2 8l5-5 5 5" stroke="#111" stroke-width="2" fill="none"/></svg></div>
  <p class="copyright">©2023. All rights reserved.</p>
</footer>

</body>
</html>
```